ULMIRA card Technical Architecture

Hello everyone ULMIRA: It is a consulting firm in Architecture and Construction. I require a card duplexing, sober, elegant, classic but not boring. Update 1: Use the following data for the card. Name: Gonzalo Pereda Mauricio Villalta Position: COO Twitter: @ulmiraAT Homepage: ulmira-example.com home address not include the participation of all thank you.

Target Market(s)

Construction companies, Architects and Consulting Engineers

Industry/Entity Type

Consulting

Contact Information for Business Card

Los campos que debe tener:
Nombre, Cargo, email, homepage y twitter

Font styles to use
Serif
Sans Serif
Other font styles liked:
• Me gustan playfair display, open sans y roboto, pero estoy sujeto a sus propuestas

Requirements
Must have
• Colors: Present combined proposals in white, red, gray and black Update 1: The two names must be clearly differentiated from the two surnames
Nice to have
• They are free to present their best proposals. I will bring them immediate feedback to the extent you can go see their designs. Complete data for card and logo files will give the winner the

```html
<!DOCTYPE html>
<html lang="es">
<head>
<meta charset="utf-8">
<title>ULMIRA – Tarjeta de presentación</title>
<link rel="stylesheet" href="https://fonts.googleapis.com/css2?family=Open+Sans:wght@400;600&display=swap">
<style>
  :root {
    --stage: #000000;
    --red-core: #b80a16;
    --red-mid: #93030c;
    --red-edge: #620005;
    --ink-light: #ffffff;
    --ink-soft: #f3dcdc;
  }
  * { margin: 0; padding: 0; box-sizing: border-box; }
  html, body {
    width: 1200px;
    height: 900px;
    overflow: hidden;
    background: var(--stage);
    font-family: "Open Sans", Arial, sans-serif;
  }
  .stage {
    position: relative;
    width: 1200px;
    height: 900px;
  }
  .card {
    position: absolute;
    top: 275px;
    width: 478px;
    height: 294px;
    color: var(--ink-light);
    background: radial-gradient(ellipse 60% 70% at 50% 45%, var(--red-core) 0%, var(--red-mid) 55%, var(--red-edge) 100%);
    overflow: hidden;
  }
  .card--back {
    left: 116px;
    border-radius: 0 50px 0 50px;
  }
  .card--front {
    left: 622px;
    border-radius: 50px 0 50px 0;
  }

  /* Back side: contact details */
  .contact {
    position: absolute;
    left: 0;
    width: 100%;
    top: 72px;
    padding-left: 0;
    text-align: center;
    transform: translateX(-2px);
  }
  .contact__block {
    display: inline-block;
    width: 160px;
    margin-left: 0;
    transform: translateX(0);
  }
  .contact__name {
    font-weight: 600;
    font-size: 17px;
    line-height: 22px;
  }
  .contact__role {
    font-size: 12.5px;
    line-height: 17px;
  }
  .contact__rule {
    width: 148px;
    height: 2px;
    margin: 14px auto 19px;
    background: var(--ink-light);
  }
  .contact__list {
    list-style: none;
    font-size: 13px;
    line-height: 19.8px;
    white-space: nowrap;
  }

  /* Front side: name lockup */
  .brand {
    position: absolute;
    left: 0;
    width: 100%;
    top: 0;
    text-align: center;
  }
  .brand__dot {
    position: absolute;
    left: 214px;
    top: 86px;
    width: 44px;
    height: 44px;
    border-radius: 50%;
    background: var(--ink-light);
  }
  .brand__name {
    position: absolute;
    left: 0;
    width: 100%;
    top: 152px;
    font-weight: 400;
    font-size: 44px;
    line-height: 50px;
    letter-spacing: 12px;
    padding-left: 12px;
  }
  .brand__rule {
    position: absolute;
    left: 94px;
    top: 199px;
    width: 290px;
    height: 1px;
    background: var(--ink-soft);
  }
  .brand__tagline {
    position: absolute;
    left: 0;
    width: 100%;
    top: 203px;
    font-size: 13px;
    line-height: 18px;
    letter-spacing: 3.4px;
    padding-left: 3px;
  }
</style>
</head>
<body>
<main class="stage">
  <section class="card card--back" aria-label="Reverso de la tarjeta">
    <div class="contact">
      <p class="contact__name">Tomas Ruvalde</p>
      <p class="contact__role">Managing Director</p>
      <div class="contact__rule"></div>
      <ul class="contact__list">
        <li>C: (044)-555-0142</li>
        <li>E: info@ulmira-example.com</li>
        <li>W: www.ulmira-example.com</li>
        <li>T: @ulmiraAT</li>
      </ul>
    </div>
  </section>

  <section class="card card--front" aria-label="Anverso de la tarjeta">
    <div class="brand">
      <span class="brand__dot"></span>
      <p class="brand__name">ULMIRA</p>
      <span class="brand__rule"></span>
      <p class="brand__tagline">ARQUITECTURA TÉCNICA</p>
    </div>
  </section>
</main>
</body>
</html>
```